Business card design needed

I run a Beautician studio (for 7 years now)
I offer
- Velmo Body Sugaring
- Ruby Glaze
- Nails
- Facials
- Manicure
- Foot Treatment
It might not be necessary to list all those treatments?
Maybe the link to the Website is sufficient?
I leave that up to you ...
(more info on www.FernAndDewByLenka.com.au)
Velmo BodySugaring is our biggest success, It replaces waxing.
I would like to incorporate the logo into the Business Card.
We had many complaints regarding our old Business Cards as the Phone Number was to small.
On the backside, we would like a "your next Appointment" section.
Looking forward to you Design, cheers ... Lenka
Industry/Entity Type
Business
Contact Information for Business Card
Fern by Dew by Lenka
14 Korrin Sqr 3942 Larkhaven
www.FernAndDewByLenka.com.au
03 9481 2267

```html
<!DOCTYPE html>
<html lang="en">
<head>
<meta charset="utf-8">
<title>Fern &amp; Dew by Lenka – Business Cards</title>
<link href="https://fonts.googleapis.com/css2?family=Ubuntu:wght@400;500&family=Open+Sans:ital,wght@0,400;1,600;1,700&family=EB+Garamond&display=swap" rel="stylesheet">
<style>
  :root {
    --backdrop: #e7e4df;
    --card: #ffffff;
    --ink: #3a3a3c;
    --ink-soft: #555557;
    --rule: #8a8a8c;
    --swoosh: #3b3b3d;
    --brand: #4a4a4a;
  }
  * { box-sizing: border-box; margin: 0; padding: 0; }
  html, body { width: 1200px; height: 788px; overflow: hidden; }
  body {
    position: relative;
    background: var(--backdrop);
    color: var(--ink);
    font-family: "Open Sans", Arial, sans-serif;
  }
  .side-label {
    position: absolute;
    font-family: "Open Sans", Arial, sans-serif;
    font-size: 20px;
    color: #222;
  }
  .card {
    position: absolute;
    width: 525px;
    height: 300px;
    background: var(--card);
    border-radius: 22px;
    overflow: hidden;
    box-shadow: 0 4px 10px rgba(0,0,0,.18);
  }
  .studio-name {
    font-family: "Ubuntu", "Trebuchet MS", sans-serif;
    font-weight: 400;
    color: var(--ink);
    letter-spacing: 1.5px;
    white-space: nowrap;
  }
  .brand-mark {
    position: absolute;
    display: flex;
    flex-direction: column;
    align-items: center;
    gap: 6px;
    font-family: "Ubuntu", "Trebuchet MS", sans-serif;
    font-weight: 500;
    color: var(--brand);
    text-align: center;
  }
  .brand-mark .dot {
    width: 30px; height: 30px; border-radius: 50%;
    background: #e79a2b;
  }
  .brand-mark .word { font-size: 19px; letter-spacing: 3px; line-height: 1; }
  .brand-mark .sub { font-size: 8px; letter-spacing: 1.5px; line-height: 1; }

  /* Front */
  .card--front { left: 341px; top: 74px; }
  .card--front .swoosh { position: absolute; inset: 0; }
  .card--front .studio-name { position: absolute; left: 21px; top: 57px; font-size: 28px; }
  .card--front .brand-mark { left: 18px; top: 172px; width: 116px; }
  .card--front .divider { position: absolute; left: 143px; top: 180px; width: 1px; height: 66px; background: var(--ink); }
  .contact { position: absolute; left: 156px; top: 172px; font-size: 16px; line-height: 27px; color: var(--ink); white-space: nowrap; }
  .contact b { font-style: italic; font-weight: 700; }

  /* Back 1 */
  .card--back1 { left: 54px; top: 444px; }
  .card--back1 .studio-name { position: absolute; left: 0; right: 0; top: 12px; text-align: center; font-size: 26px; }
  .card--back1 .title-rule { position: absolute; left: 0; right: 0; top: 50px; height: 1px; background: var(--rule); }
  .heading { font-style: italic; font-weight: 700; color: var(--ink); }
  .offer { position: absolute; left: 29px; top: 68px; }
  .offer .heading { font-size: 18px; display: block; margin-bottom: 4px; }
  .offer ul { list-style: none; font-family: "EB Garamond", Georgia, serif; font-size: 15px; color: var(--ink-soft); line-height: 20px; }
  .offer li::before { content: ""; display: inline-block; width: 5px; height: 5px; background: var(--ink); margin: 0 7px 2px 0; vertical-align: middle; }
  .column-rule { position: absolute; left: 207px; top: 84px; width: 2px; height: 128px; background: linear-gradient(#fff, #6b6b6b 50%, #fff); }
  .appointment { position: absolute; left: 243px; top: 68px; width: 270px; }
  .appointment .heading { font-size: 18px; display: block; margin-bottom: 12px; }
  .fill-row { display: flex; align-items: flex-end; font-size: 16px; color: var(--ink); height: 33px; margin-bottom: 4px; }
  .fill-row .blank { flex: 1; border-bottom: 1px solid var(--ink); margin: 0 4px 4px 0; }
  .card--back1 .hours { position: absolute; left: 0; right: 0; top: 237px; text-align: center; }
  .card--back1 .hours .heading { font-size: 14px; display: block; }
  .card--back1 .hours p { font-size: 12.5px; margin-top: 4px; }
  .card--back1 .hours span + span { margin-left: 24px; }

  /* Back 2 */
  .card--back2 { left: 622px; top: 444px; }
  .card--back2 .hours-title { position: absolute; left: 32px; top: 27px; font-size: 20px; letter-spacing: 1.2px; }
  .card--back2 .hours-list { position: absolute; left: 29px; top: 59px; font-size: 18px; line-height: 24px; }
  .card--back2 .brand-mark { left: 378px; top: 30px; width: 116px; }
  .card--back2 .section-rule { position: absolute; left: 28px; right: 30px; top: 116px; height: 1px; background: #b5b5b5; }
  .next-visit { position: absolute; left: 45px; top: 140px; display: flex; align-items: flex-end; font-size: 19px; }
  .next-visit .blank { width: 260px; border-bottom: 1px solid var(--ink); margin: 0 3px 5px 0; }
  .date-row { position: absolute; left: 34px; top: 191px; display: flex; align-items: flex-end; font-size: 19px; gap: 6px; white-space: nowrap; }
  .date-row .blank { display: inline-block; border-bottom: 1px solid var(--ink); margin-bottom: 5px; }
  .weekdays { position: absolute; left: 58px; top: 248px; display: flex; font-size: 17px; }
  .weekdays label { display: flex; align-items: center; margin-right: 14px; }
  .weekdays .box { width: 23px; height: 23px; border: 1px solid var(--ink); margin-right: 10px; }
</style>
</head>
<body>

  <div class="side-label" style="left:573px; top:34px;">Front</div>
  <div class="side-label" style="left:286px; top:404px;">Back - 1</div>
  <div class="side-label" style="left:858px; top:404px;">Back - 2</div>

  <section class="card card--front">
    <svg class="swoosh" width="525" height="300" viewBox="0 0 525 300" aria-hidden="true">
      <path d="M372 0 C468 40 500 170 448 300 L525 300 L525 0 Z" fill="var(--swoosh)"/>
      <path d="M412 0 C482 50 508 160 470 300 L488 300 C530 160 500 40 440 0 Z" fill="#ffffff"/>
    </svg>
    <h1 class="studio-name">FERN&amp;DEW BY LENKA</h1>
    <div class="brand-mark">
      <span class="dot"></span>
      <span class="word">VELMO</span>
      <span class="sub">BODY SUGARING</span>
    </div>
    <span class="divider"></span>
    <div class="contact">
      <div><b>phone</b> 03 9481 2267</div>
      <div><b>add</b> 14 Korrin Sqr, 3942 Larkhaven</div>
      <div><b>web</b> www.FernAndDewByLenka.com.au</div>
    </div>
  </section>

  <section class="card card--back1">
    <h2 class="studio-name">FERN&amp;DEW BY LENKA</h2>
    <span class="title-rule"></span>
    <div class="offer">
      <span class="heading">I offer</span>
      <ul>
        <li>Velmo Body Sugaring</li>
        <li>Ruby Glaze</li>
        <li>Nails</li>
        <li>Facials</li>
        <li>Manicure</li>
        <li>Foot Treatment</li>
      </ul>
    </div>
    <span class="column-rule"></span>
    <div class="appointment">
      <span class="heading">An Appointment</span>
      <div class="fill-row">Name<span class="blank"></span></div>
      <div class="fill-row">Date<span class="blank"></span></div>
      <div class="fill-row">time<span class="blank"></span>am / pm</div>
    </div>
    <div class="hours">
      <span class="heading">Hours of Operation</span>
      <p><span>Mon. to Fri.&nbsp; 7.30am - 7.00pm</span><span>Sat. 7.30am - 12.00pm</span></p>
    </div>
  </section>

  <section class="card card--back2">
    <h2 class="heading hours-title">Hours of Operation</h2>
    <div class="hours-list">
      <div>Monday to Friday -&nbsp; 7.30am - 7.00pm</div>
      <div>Saturday - 7.30am - 12.00pm</div>
    </div>
    <div class="brand-mark">
      <span class="dot"></span>
      <span class="word">VELMO</span>
      <span class="sub">BODY SUGARING</span>
    </div>
    <span class="section-rule"></span>
    <div class="next-visit"><span class="blank"></span>has an appointment</div>
    <div class="date-row">
      Date :<span class="blank" style="width:40px"></span>/<span class="blank" style="width:42px"></span>/<span class="blank" style="width:52px"></span>@<span class="blank" style="width:42px"></span>:<span class="blank" style="width:52px"></span>am / pm
    </div>
    <div class="weekdays">
      <label><span class="box"></span>Mon.</label>
      <label><span class="box"></span>Tue.</label>
      <label><span class="box"></span>Wed.</label>
      <label><span class="box"></span>Thu.</label>
      <label><span class="box"></span>Fri.</label>
    </div>
  </section>

</body>
</html>
```